Financial Advisor Resource Firm needs business card design

Need business card design for company in Omaha NE called Meridale Circle. We provide resources to financial advisors....workshop programs, retirement analysis, and insurance planning. I would like to see designs that use grays, greens, black, and white colors. The final design should communicate 'collaboration' and be simple yet attractive to financial planning clients. I will attached our logo and another picture of a puzzle piece coming together. I would like the incorporate the puzzle picture somehow, maybe on the back somehow, with color or just the gray scale....OR, the picture be the front of the card with 'Meridale' definition on it (see upload) and then company logo, employee name, title, address on the back (see ppt uploaded). The following disclosure needs to be included somewhere- Advisory services offered through Stonebrook Assets, LLC.
Updates

I uploaded a svg and ai file of the logo

Target Market(s)

Financial planning clients and financial advisors....so pretty diverse age range of about 40-70.

Industry/Entity Type

Financial Planning

Contact Information for Business Card

Tobias L. Fenwright, MBA
Founder/President
5287 E. Larkin Road
Suite 230
Omaha, NE 68190
Phone- (402) 555-0147
Cell- (402) 555-0183
Fax- (402) 555-0129
email- tobias@meridaleplan.example
web address- www.meridaleplan.example

Colors
1b1b1b
474747
d3d3d3
ffffff
9bcb3c
abd036

Requirements
Must have
• Must include logo provided, must be 2 sided, and must have disclosure...all of these items listed in project description

```html
<!DOCTYPE html>
<html lang="en">
<head>
<meta charset="utf-8">
<title>Meridale Circle — Business Card</title>
<link href="https://fonts.googleapis.com/css2?family=Arimo:wght@400;700&display=swap" rel="stylesheet">
<style>
  :root {
    --ink: #1b1b1b;
    --graphite: #474747;
    --silver: #d3d3d3;
    --paper: #ffffff;
    --leaf: #9bcb3c;
    --lime: #abd036;
    --leaf-deep: #7fb52f;
    --backdrop: #ecece8;
  }
  * { box-sizing: border-box; margin: 0; padding: 0; }
  html, body { width: 1200px; height: 900px; overflow: hidden; }
  body {
    background: var(--backdrop);
    font-family: "Arimo", Arial, sans-serif;
    position: relative;
  }
  .card {
    position: absolute;
    left: 260px;
    width: 680px;
    height: 388px;
    overflow: hidden;
    box-shadow: 0 6px 18px rgba(0,0,0,0.18);
  }
  .card--back { top: 40px; }
  .card--front { top: 472px; background: var(--paper); }

  /* Back */
  .back-photo {
    position: absolute; inset: 0;
    background: radial-gradient(ellipse at 60% 45%, #a9d56a 0%, #8cc14a 45%, #6fab38 100%);
  }
  .back-brand {
    position: absolute; left: 0; right: 0; top: 150px;
    display: flex; align-items: center; justify-content: center; gap: 14px;
  }
  .back-brand .brand-dot {
    width: 22px; height: 22px; border-radius: 50%; background: var(--paper);
  }
  .back-brand .brand-name {
    font-size: 40px; font-weight: 400; color: var(--paper);
    letter-spacing: 2px; text-transform: uppercase;
  }
  .disclosure {
    position: absolute; left: 0; right: 0; top: 232px;
    text-align: center; color: var(--paper); font-size: 15px; letter-spacing: 0.3px;
  }

  /* Front */
  .front-art { position: absolute; inset: 0; }
  .brand {
    position: absolute; left: 44px; top: 44px;
    display: flex; align-items: center; gap: 10px;
  }
  .brand .brand-dot {
    width: 18px; height: 18px; border-radius: 50%; background: var(--leaf);
  }
  .brand .brand-name {
    font-size: 32px; font-weight: 400; color: var(--ink);
    letter-spacing: 1.5px; text-transform: uppercase;
  }
  .person { position: absolute; left: 44px; top: 140px; }
  .person-name { font-size: 22px; font-weight: 700; color: var(--leaf); }
  .person-title { font-size: 14px; color: var(--graphite); margin-top: 3px; }

  .address {
    position: absolute; left: 44px; top: 282px;
    color: var(--paper); font-size: 14px; line-height: 1.45; opacity: 0.92;
  }
  .contacts {
    position: absolute; right: 30px; top: 256px;
    list-style: none; color: var(--paper); font-size: 14px; line-height: 1;
  }
  .contacts li {
    display: flex; justify-content: flex-end; align-items: center;
    gap: 10px; height: 20px;
  }
  .contacts svg { width: 13px; height: 13px; flex: none; }
</style>
</head>
<body>

<section class="card card--back" aria-label="Card back">
  <div class="back-photo" role="img" aria-label="Green-toned photograph of hands fitting puzzle pieces together"></div>
  <div class="back-brand">
    <span class="brand-dot"></span>
    <span class="brand-name">Meridale Circle</span>
  </div>
  <p class="disclosure">Advisory services offered through Stonebrook Assets, LLC</p>
</section>

<section class="card card--front" aria-label="Card front">
  <svg class="front-art" width="680" height="388" viewBox="0 0 680 388" aria-hidden="true">
    <defs>
      <linearGradient id="band" x1="0" y1="0" x2="1" y2="1">
        <stop offset="0" stop-color="#9bcb3c"/>
        <stop offset="1" stop-color="#abd036"/>
      </linearGradient>
      <linearGradient id="sheen" x1="0" y1="0" x2="0" y2="1">
        <stop offset="0" stop-color="#ffffff"/>
        <stop offset="1" stop-color="#ececec"/>
      </linearGradient>
    </defs>
    <rect width="680" height="388" fill="url(#sheen)"/>
    <path d="M120 232 Q440 236 680 170 L680 184 Q440 244 140 236 Z" fill="#474747"/>
    <path d="M140 236 Q440 244 680 184 L680 192 Q450 250 160 240 Z" fill="#d3d3d3"/>
    <path d="M0 240 Q430 252 680 196 L680 388 L0 388 Z" fill="url(#band)"/>
  </svg>

  <div class="brand">
    <span class="brand-dot"></span>
    <span class="brand-name">Meridale Circle</span>
  </div>

  <div class="person">
    <p class="person-name">Tobias L. Fenwright, MBA</p>
    <p class="person-title">Founder/President</p>
  </div>

  <address class="address" style="font-style:normal">
    5287 E. Larkin Road<br>
    Suite 230, Omaha, NE 68190
  </address>

  <ul class="contacts">
    <li>(402) 555-0147
      <svg viewBox="0 0 16 16"><path d="M4 1l3 3-2 2c1 2 3 4 5 5l2-2 3 3-2 3C7 15 1 9 1 3z" fill="#fff"/></svg>
    </li>
    <li>(402) 555-0183
      <svg viewBox="0 0 16 16"><rect x="4" y="1" width="8" height="14" rx="1.5" fill="none" stroke="#fff" stroke-width="1.6"/></svg>
    </li>
    <li>(402) 555-0129
      <svg viewBox="0 0 16 16"><rect x="4" y="1" width="8" height="5" fill="#fff"/><rect x="1" y="6" width="14" height="7" rx="1" fill="#fff"/></svg>
    </li>
    <li>tobias@meridaleplan.example
      <svg viewBox="0 0 16 16"><rect x="1" y="3" width="14" height="10" fill="none" stroke="#fff" stroke-width="1.5"/><path d="M1 3l7 6 7-6" fill="none" stroke="#fff" stroke-width="1.5"/></svg>
    </li>
    <li>www.meridaleplan.example
      <svg viewBox="0 0 16 16"><circle cx="8" cy="8" r="7" fill="#fff"/><path d="M1 8h14M8 1c-3 4-3 10 0 14M8 1c3 4 3 10 0 14" fill="none" stroke="#9bcb3c" stroke-width="1"/></svg>
    </li>
  </ul>
</section>

</body>
</html>
```